Vorn upkeep KT Solar Venture

Solar power system install
Services and maintenance
wiring, Rewinding and Renovation
Switch Board Upgrade
Power and lighting point
t doesn’t matter how much you spend on quality parts, your solar system will let you down if your design and installation are sub-par. Have your solar system tailored and installed by our Master Electrician and Bright Grid Guild Accredited team.

Target Market(s)

sales and installed

Industry/Entity Type

Solar install and retailer

Contact Information for Business Card

Name , Email, Phone Number ,Business address,

Font styles to use
Serif

Colors
0054AA
0677BA
7BADD7
CADEEF
E8F1F8

Requirements
Must have
• clear and bright
Nice to have
• new design
Should not have
• unclear pictures

```html
<!DOCTYPE html>
<html lang="en">
<head>
<meta charset="utf-8">
<title>Vorn Upkeep – Business Card</title>
<link href="https://fonts.googleapis.com/css2?family=Roboto:wght@400;500;700&family=Roboto+Condensed:wght@700&display=swap" rel="stylesheet">
<style>
  :root {
    --page: #2e2e2e;
    --blue-deep: #0054AA;
    --blue-mid: #0677BA;
    --blue-soft: #7BADD7;
    --green: #5aae3c;
    --green-dark: #1d8a3c;
    --band: #e9eaeb;
    --ink: #1f1f1f;
    --card-white: #f2f2f2;
    --white: #ffffff;
  }
  * { margin: 0; padding: 0; box-sizing: border-box; }
  html, body { width: 1200px; height: 1138px; overflow: hidden; }
  body {
    background: var(--page);
    position: relative;
    font-family: "Roboto", Arial, sans-serif;
  }
  .card {
    position: absolute;
    border-radius: 14px;
    overflow: hidden;
  }
  /* ---------- front ---------- */
  .card-front {
    left: 274px; top: 186px; width: 623px; height: 376px;
    background: linear-gradient(120deg, var(--blue-mid) 0%, #17898f 40%, #3f9f6a 70%, var(--green) 100%);
  }
  .brand {
    position: absolute;
    display: flex;
    align-items: center;
  }
  .brand-dot {
    width: 64px; height: 64px; border-radius: 50%;
    background: #f2b01e;
    flex-shrink: 0;
  }
  .brand-name {
    font-family: "Roboto Condensed", "Arial Narrow", sans-serif;
    font-weight: 700;
    text-transform: uppercase;
    line-height: 1.08;
  }
  .card-front .brand { left: 150px; top: 100px; gap: 22px; }
  .card-front .brand-name { color: var(--white); font-size: 32px; letter-spacing: 0.5px; }
  .services-band {
    position: absolute; left: 0; top: 239px; width: 100%; height: 73px;
    background: linear-gradient(180deg, #f3f3f3, #dedfe0);
    display: flex; flex-direction: column; justify-content: center; align-items: center;
    gap: 4px;
    color: var(--ink); font-size: 16.5px; letter-spacing: 0.1px;
  }
  .services-band .sep { margin: 0 6px; }
  .web-line {
    position: absolute; left: 0; top: 331px; width: 100%;
    display: flex; justify-content: center; align-items: center; gap: 24px;
    color: var(--white); font-size: 15.5px;
  }
  .web-line .rule { width: 80px; height: 1.5px; background: rgba(255,255,255,0.75); }
  /* ---------- back ---------- */
  .card-back {
    left: 276px; top: 608px; width: 618px; height: 374px;
    background: var(--card-white);
  }
  .card-back .brand {
    left: 52px; top: 110px; width: 230px;
    flex-direction: column; gap: 16px;
  }
  .card-back .brand-dot { width: 80px; height: 80px; }
  .card-back .brand-name { color: var(--blue-deep); font-size: 28px; text-align: center; }
  .contact {
    position: absolute; left: 354px; top: 84px;
    color: var(--ink);
  }
  .contact .person { color: var(--blue-deep); font-size: 25px; font-weight: 500; line-height: 1.2; }
  .contact .role { font-size: 16px; margin-top: 2px; }
  .contact .address { font-size: 16px; line-height: 24px; margin-top: 24px; }
  .contact ul { list-style: none; margin-top: 10px; }
  .contact li {
    display: flex; align-items: center; font-size: 16px; height: 24px;
  }
  .contact li svg { width: 14px; height: 14px; margin-right: 18px; fill: var(--green-dark); }
</style>
</head>
<body>

<section class="card card-front">
  <div class="brand">
    <span class="brand-dot"></span>
    <div class="brand-name">Vorn Upkeep<br>Solar Venture</div>
  </div>
  <div class="services-band">
    <p>Solar Power System Install<span class="sep">|</span>Wiring, Rewinding &amp; Renovation</p>
    <p>Services &amp; Maintenance<span class="sep">|</span>Switch Board Upgrade<span class="sep">|</span>Power &amp; Lighting Point</p>
  </div>
  <div class="web-line">
    <span class="rule"></span>
    <span>www.ktsolarventure.com</span>
    <span class="rule"></span>
  </div>
</section>

<section class="card card-back">
  <div class="brand">
    <span class="brand-dot"></span>
    <div class="brand-name">Vorn Upkeep<br>Solar Venture</div>
  </div>
  <div class="contact">
    <p class="person">Mara Lindqvist</p>
    <p class="role">Managing Director</p>
    <p class="address">58 Harrow Lane, Elmford,<br>Brookvale, US 204718</p>
    <ul>
      <li>
        <svg viewBox="0 0 16 16" aria-hidden="true"><path d="M2 5c0-2 2-3 6-3s6 1 6 3v1h-3V4.5H5V6H2z M4 7h8l2 7H2z"/></svg>
        555-274-0193
      </li>
      <li>
        <svg viewBox="0 0 16 16" aria-hidden="true"><path d="M1 3h14v10H1z M2.5 4.5v.4L8 9l5.5-4.1v-.4z" fill-rule="evenodd"/></svg>
        mara@ktsolarventure.com
      </li>
      <li>
        <svg viewBox="0 0 16 16" aria-hidden="true"><path d="M8 1a7 7 0 1 0 0 14A7 7 0 0 0 8 1zm0 1.5c.8 1 1.4 2.5 1.6 4.5H6.4C6.6 5 7.2 3.5 8 2.5zM2.6 7h2.3c.1-1.6.5-3 1.1-4A5.5 5.5 0 0 0 2.6 7zm8.5 0h2.3A5.5 5.5 0 0 0 10 3c.6 1 1 2.4 1.1 4zM2.6 9A5.5 5.5 0 0 0 6 13c-.6-1-1-2.4-1.1-4zm3.8 0c.2 2 .8 3.5 1.6 4.5.8-1 1.4-2.5 1.6-4.5zm4.7 0c-.1 1.6-.5 3-1.1 4a5.5 5.5 0 0 0 3.4-4z"/></svg>
        www.ktsolarventure.com
      </li>
    </ul>
  </div>
</section>

</body>
</html>
```